Stationery Design Task - Stationary, memo and report templates for professional services company

Looking for someone to update stationary design but just as importantly come up with a template for reports and memos for use in our consulting firm. Would also like some brand use guidelines to be able to share with our whole team. We have an existing logo that we like. Need to update with a more contemporary look so that our deliverables to clients look good and professional yet stylish. This is for business to business communications. No need for envelope design. Important to have design for multiple pages, i.e. first page of a report and then 2nd page. Need to use in MS word documents so must be easy to use and replicate. Don't want something overly complex. Clean, fresh looking is best.

Industry/Entity Type

Information Technology

Font styles to use
Sans Serif

Colors
33a6d7
0792cd
85cae6
cee9f5
cedeed
85abd2
3377b5
0455a3

Requirements
Must have
• Clean look but with a little style or pop. Something that can easily be used in word documents. Need to have page styles that have a first page of a report (not a cover page) and then secondary page.
Nice to have
• - Although the dark blue is our primary color. Might be willing to look at some accent color as well.
Should not have
• Not just our logo on the page with a color bar.

```html
<!DOCTYPE html>
<html lang="en">
<head>
<meta charset="utf-8">
<title>Crestline Systems Letterhead</title>
<link rel="stylesheet" href="https://fonts.googleapis.com/css2?family=PT+Sans:ital,wght@1,400&family=Roboto:wght@400;700&display=swap">
<style>
  :root {
    --stage: #cdcdcd;
    --headline: #1d6b64;
    --paper: #f7f7f7;
    --navy: #0455a3;
    --blue: #0792cd;
    --sky: #33a6d7;
    --cyan: #1fd2ef;
    --brand: #2f7fcf;
    --ink: #2a2a2a;
    --muted: #7a8594;
    --divider: #c9d3de;
    --deco: #e4e4e4;
    --card: #ffffff;
  }
  * { box-sizing: border-box; margin: 0; padding: 0; }
  html, body { width: 1200px; height: 710px; overflow: hidden; }
  body {
    background: var(--stage);
    font-family: "Roboto", Arial, sans-serif;
    position: relative;
  }
  .headline {
    position: absolute; top: 18px; left: 0; width: 1200px;
    text-align: center;
    font-family: "PT Sans", "Trebuchet MS", sans-serif;
    font-weight: 400; font-style: italic; font-size: 50px; color: var(--headline);
  }
  .sheets {
    position: absolute; top: 110px; left: 29px;
    display: flex; gap: 40px;
  }
  .sheet {
    position: relative; width: 354px; height: 500px;
    background: var(--paper); overflow: hidden;
    box-shadow: 0 10px 18px rgba(0,0,0,.18);
  }
  .sheet__band {
    position: absolute; left: 0; top: 0; bottom: 0; width: 30px;
    background: linear-gradient(180deg, var(--navy) 0%, var(--blue) 35%, var(--sky) 65%, var(--cyan) 100%);
  }
  .sheet__rule {
    position: absolute; top: 0; left: 30px; right: 0; height: 2px; background: var(--sky);
  }
  .brand {
    position: absolute; top: 10px; left: 12px;
    display: flex; align-items: center; gap: 6px;
    background: var(--card); border-radius: 6px; padding: 7px 10px 7px 8px;
    box-shadow: 0 1px 3px rgba(0,0,0,.12);
  }
  .brand__dot { width: 16px; height: 16px; border-radius: 50%; background: var(--brand); flex: none; }
  .brand__name {
    display: flex; flex-direction: column;
    font-weight: 700; color: var(--brand); line-height: 1;
  }
  .brand__word { font-size: 16px; letter-spacing: .2px; }
  .brand__word--small { font-size: 6.5px; letter-spacing: 3.1px; margin-top: 2px; }
  .contact {
    position: absolute; top: 16px; left: 134px;
    border-left: 1px solid var(--divider); padding-left: 8px;
    font-size: 6px; line-height: 9px; color: var(--muted);
  }
  .contact__row { display: flex; align-items: center; gap: 3px; white-space: nowrap; }
  .contact__row--lead { color: var(--brand); font-weight: 700; }
  .contact svg { width: 6px; height: 6px; flex: none; }
  .letter {
    position: absolute; top: 78px; left: 52px; right: 26px; z-index: 1;
    font-size: 6.4px; line-height: 9px; color: var(--ink);
  }
  .letter p { margin-bottom: 9px; }
  .globe {
    position: absolute; right: -40px; bottom: -40px;
    width: 270px; height: 270px; border-radius: 50%;
    background: radial-gradient(circle at 45% 45%, var(--deco) 0%, rgba(228,228,228,.6) 60%, rgba(228,228,228,0) 72%);
  }
</style>
</head>
<body>
  <h1 class="headline">Easy to use in Word Format</h1>

  <main class="sheets">
    <section class="sheet sheet--letter">
      <div class="globe" role="img" aria-label="Faint watermark decoration"></div>
      <div class="sheet__band"></div>
      <div class="sheet__rule"></div>
      <div class="brand"><span class="brand__dot"></span><span class="brand__name"><span class="brand__word">CRESTLINE</span><span class="brand__word brand__word--small">SYSTEMS</span></span></div>
      <div class="contact">
        <div class="contact__row contact__row--lead">
          <svg viewBox="0 0 10 10"><path d="M5 0a3.5 3.5 0 0 0-3.5 3.5C1.5 6 5 10 5 10s3.5-4 3.5-6.5A3.5 3.5 0 0 0 5 0z" fill="#2f7fcf"/></svg>
          120 Harbor Lane, Fairview, KS 66012
        </div>
        <div class="contact__row">
          <svg viewBox="0 0 10 10"><rect width="10" height="10" rx="2" fill="#2f7fcf"/></svg>
          (555) 014 2280 &nbsp;
          <svg viewBox="0 0 10 10"><rect width="10" height="10" rx="2" fill="#2f7fcf"/></svg>
          hello@crestlinesystems.com
        </div>
        <div class="contact__row">
          <svg viewBox="0 0 10 10"><circle cx="5" cy="5" r="5" fill="#85abd2"/></svg>
          www.crestlinesystems.com
        </div>
      </div>
      <article class="letter">
        <p>Lorem Ipsum is simply dummy text of the printing and typesetting industry. Lorem Ipsum has been the industry's standard dummy text ever since the 1500s, when an unknown printer took a galley of type and scrambled it to make a type specimen book. It has survived not only five centuries, but also the leap into electronic typesetting, remaining essentially unchanged. It was popularised in the 1960s with the release of Typeworks sheets containing Lorem Ipsum passages, and more recently with desktop publishing software like PageCraft Studio including versions of Lorem Ipsum.</p>
        <p>It is a long established fact that a reader will be distracted by the readable content of a page when looking at its layout. The point of using Lorem Ipsum is that it has a more-or-less normal distribution of letters, as opposed to using 'Content here, content here', making it look like readable English. Many desktop publishing packages and web page editors now use Lorem Ipsum as their default model text, and a search for 'lorem ipsum' will uncover many web sites still in their infancy. Various versions have evolved over the years, sometimes by accident, sometimes on purpose (injected humour and the like).</p>
        <p>Contrary to popular belief, Lorem Ipsum is not simply random text. It has roots in a piece of classical Latin literature from 45 BC, making it over 2000 years old. Edwin Marlow, a Latin professor at Northgate College in Westbrook, looked up one of the more obscure Latin words, consectetur, from a Lorem Ipsum passage, and going through the cites of the word in classical literature, discovered the undoubtable source. Lorem Ipsum comes from sections 1.10.32 and 1.10.33 of an old treatise on ethics. The generated Lorem Ipsum is therefore always free from repetition, injected humour, or non-characteristic words etc.</p>
      </article>
    </section>

    <section class="sheet sheet--first">
      <div class="globe" role="img" aria-label="Faint watermark decoration"></div>
      <div class="sheet__band"></div>
      <div class="sheet__rule"></div>
      <div class="brand"><span class="brand__dot"></span><span class="brand__name"><span class="brand__word">CRESTLINE</span><span class="brand__word brand__word--small">SYSTEMS</span></span></div>
    </section>

    <section class="sheet sheet--continuation">
      <div class="globe" role="img" aria-label="Faint watermark decoration"></div>
      <div class="sheet__band"></div>
      <div class="sheet__rule"></div>
      <div class="brand"><span class="brand__dot"></span><span class="brand__name"><span class="brand__word">CRESTLINE</span><span class="brand__word brand__word--small">SYSTEMS</span></span></div>
    </section>
  </main>
</body>
</html>
```